Dunmore Roofing

Want a professional looking business card

Industry/Entity Type

Business

Contact Information for Business Card

Paul Dunmore ( Owner) paul@dunmoreroofing-example.com, www.dunmoreroofing-example.com, Adress: 4172 Township road 43 Larkfield,NB K9X4T2

```html
<!DOCTYPE html>
<html lang="en">
<head>
<meta charset="utf-8">
<title>Dunmore Roofing – Business Card</title>
<link rel="stylesheet" href="https://fonts.googleapis.com/css2?family=Roboto:wght@400;500;700&family=Roboto+Condensed:wght@700&display=swap">
<style>
  :root {
    --brand-blue: #1d4584;
    --steel-grey: #7c7f84;
    --light-grey: #c9cbce;
    --ink: #222428;
    --paper: #ffffff;
    --backdrop: #ece9ea;
  }
  * { margin: 0; padding: 0; box-sizing: border-box; }
  html, body { width: 1200px; height: 900px; overflow: hidden; }
  body {
    background: var(--backdrop);
    font-family: "Roboto", Arial, sans-serif;
    position: relative;
  }
  .card {
    position: absolute;
    left: 320px;
    width: 560px;
    height: 320px;
    overflow: hidden;
    box-shadow: 0 6px 18px rgba(0,0,0,0.18);
  }
  /* Front side */
  .card--front {
    top: 70px;
    background: var(--brand-blue);
    color: var(--paper);
  }
  .card--front .brand-mark {
    position: absolute;
    left: 50%;
    top: 58px;
    width: 34px; height: 34px;
    margin-left: -17px;
    border-radius: 50%;
    background: var(--paper);
  }
  .card--front .brand-name {
    position: absolute;
    left: 0; right: 0;
    top: 108px;
    text-align: center;
    font-family: "Roboto Condensed", Arial, sans-serif;
    font-weight: 700;
    font-size: 46px;
    letter-spacing: 4px;
    text-transform: uppercase;
    color: var(--paper);
  }
  .card--front .website {
    position: absolute;
    left: 0; right: 0;
    bottom: 62px;
    text-align: center;
    font-size: 15px;
    letter-spacing: 0.3px;
  }
  /* Back side */
  .card--back {
    top: 500px;
    background: var(--paper);
  }
  .card--back .shapes { position: absolute; inset: 0; }
  .card--back .brand-block {
    position: absolute;
    left: 30px;
    top: 104px;
    width: 230px;
    text-align: center;
  }
  .card--back .brand-mark {
    display: block;
    width: 26px; height: 26px;
    margin: 0 auto 10px;
    border-radius: 50%;
    background: var(--brand-blue);
  }
  .card--back .brand-name {
    font-family: "Roboto Condensed", Arial, sans-serif;
    font-weight: 700;
    font-size: 27px;
    letter-spacing: 2px;
    line-height: 1.15;
    text-transform: uppercase;
    color: var(--brand-blue);
  }
  .contact {
    position: absolute;
    left: 300px;
    top: 92px;
    color: var(--ink);
  }
  .contact .person-name {
    font-family: "Roboto Condensed", Arial, sans-serif;
    font-weight: 700;
    font-size: 24px;
    color: var(--brand-blue);
    line-height: 1;
  }
  .contact .person-role {
    font-size: 13px;
    margin: 3px 0 12px;
  }
  .contact .address { font-size: 13px; line-height: 1.35; margin-bottom: 6px; }
  .contact .line {
    display: flex;
    align-items: center;
    gap: 7px;
    font-size: 13px;
    line-height: 1.45;
    white-space: nowrap;
  }
  .contact .line svg { width: 12px; height: 12px; flex: none; }
</style>
</head>
<body>

  <section class="card card--front" aria-label="Business card front">
    <span class="brand-mark"></span>
    <div class="brand-name">Dunmore Roofing</div>
    <div class="website">www.dunmoreroofing-example.com</div>
  </section>

  <section class="card card--back" aria-label="Business card back">
    <svg class="shapes" viewBox="0 0 560 320" preserveAspectRatio="none" aria-hidden="true">
      <path d="M360 0 H560 V200 C525 110 465 40 360 0 Z" fill="var(--brand-blue)"/>
      <path d="M0 150 C90 250 230 310 390 320 H0 Z" fill="var(--light-grey)"/>
      <path d="M0 190 C90 270 210 312 330 320 H0 Z" fill="var(--steel-grey)"/>
      <line x1="285" y1="85" x2="270" y2="215" stroke="var(--brand-blue)" stroke-width="1.5"/>
    </svg>

    <div class="brand-block">
      <span class="brand-mark"></span>
      <div class="brand-name">Dunmore<br>Roofing</div>
    </div>

    <div class="contact">
      <div class="person-name">Paul Dunmore</div>
      <div class="person-role">Owner</div>
      <div class="address">4172 Township road 43<br>Larkfield,NB K9X4T2</div>
      <div class="line">
        <svg viewBox="0 0 24 24"><path fill="var(--brand-blue)" d="M6.6 10.8a15 15 0 0 0 6.6 6.6l2.2-2.2c.3-.3.7-.4 1-.2 1.1.4 2.3.6 3.6.6.6 0 1 .4 1 1V20c0 .6-.4 1-1 1A17 17 0 0 1 3 4c0-.6.4-1 1-1h3.5c.6 0 1 .4 1 1 0 1.3.2 2.5.6 3.6.1.3 0 .7-.2 1z"/></svg>
        (555) 014-2278
      </div>
      <div class="line">
        <svg viewBox="0 0 24 24"><rect x="2" y="5" width="20" height="14" rx="1" fill="var(--brand-blue)"/><path d="M3 6l9 7 9-7" fill="none" stroke="#fff" stroke-width="1.6"/></svg>
        paul@dunmoreroofing-example.com
      </div>
      <div class="line">
        <svg viewBox="0 0 24 24"><circle cx="12" cy="12" r="10" fill="var(--brand-blue)"/><path d="M2 12h20M12 2c3 3 3 17 0 20M12 2c-3 3-3 17 0 20" fill="none" stroke="#fff" stroke-width="1.4"/></svg>
        www.dunmoreroofing-example.com
      </div>
    </div>
  </section>

</body>
</html>
```